Business Card Design

We need a business card designed for our new company. Prefer a black card with white logo & writing.

Contact Information for Business Card

Ted Galloway, address: 7-4812 Fernhollow Road, Abbotsford, BC, V3K 8R2, Office Phone: 604-712-3390, Cell: 604-947-2164, Email: ted@resinworkshub.ca

Colors

Designer to choose only greyscale colors for use in the design.

```html
<!DOCTYPE html>
<html lang="en">
<head>
<meta charset="utf-8">
<title>Resinworks Hub – Business Card</title>
<link href="https://fonts.googleapis.com/css2?family=Montserrat:wght@400;700&display=swap" rel="stylesheet">
<style>
  :root {
    --backdrop: #222222;
    --card: #000000;
    --ink: #ffffff;
    --ink-soft: #e6e6e6;
  }
  * { margin: 0; padding: 0; box-sizing: border-box; }
  html, body {
    width: 1200px; height: 900px; overflow: hidden;
    background: var(--backdrop);
    font-family: "Montserrat", Arial, sans-serif;
    color: var(--ink);
  }
  .card {
    position: absolute;
    left: 341px;
    width: 518px;
    height: 296px;
    background: var(--card);
  }
  .card--front { top: 141px; }
  .card--back { top: 463px; }

  .brand-disc {
    position: absolute;
    left: 88px; top: 89px;
    width: 124px; height: 118px;
    border-radius: 50%;
    background: var(--ink);
    color: var(--card);
    display: flex; align-items: center; justify-content: center;
    text-align: center;
    font-weight: 700; font-size: 13px; line-height: 1.2;
    letter-spacing: 0.5px;
  }
  .divider {
    position: absolute;
    left: 238px; top: 89px;
    width: 1.5px; height: 118px;
    background: var(--ink);
  }
  .contact {
    position: absolute;
    left: 265px; top: 85px;
  }
  .contact__name {
    font-weight: 700; font-size: 18px; line-height: 1.1;
    letter-spacing: 0.2px;
  }
  .contact__title {
    font-size: 13px; margin-top: 2px;
    color: var(--ink-soft);
  }
  .contact__list {
    list-style: none;
    margin-top: 16px;
  }
  .contact__item {
    display: flex; align-items: center;
    font-size: 13px; line-height: 18px;
    color: var(--ink-soft);
  }
  .contact__icon {
    width: 12px; height: 12px;
    margin-right: 5px;
    fill: var(--ink);
    flex: none;
  }
  .address {
    position: absolute;
    left: 0; right: 0; top: 255px;
    text-align: center;
    font-size: 13px;
    color: var(--ink-soft);
  }
  .wordmark {
    position: absolute;
    inset: 0;
    display: flex; align-items: center; justify-content: center;
    font-weight: 700; font-size: 36px;
    letter-spacing: 1px;
    color: var(--ink);
  }
</style>
</head>
<body>
  <section class="card card--front">
    <div class="brand-disc">RESINWORKS<br>HUB</div>
    <div class="divider"></div>
    <div class="contact">
      <p class="contact__name">TED GALLOWAY</p>
      <p class="contact__title">President</p>
      <ul class="contact__list">
        <li class="contact__item">
          <svg class="contact__icon" viewBox="0 0 24 24"><path d="M6.6 10.8a15.2 15.2 0 0 0 6.6 6.6l2.2-2.2c.3-.3.7-.4 1-.2 1.1.4 2.3.6 3.6.6.6 0 1 .4 1 1V20c0 .6-.4 1-1 1A17 17 0 0 1 3 4c0-.6.4-1 1-1h3.5c.6 0 1 .4 1 1 0 1.3.2 2.5.6 3.6.1.3 0 .7-.2 1z"/></svg>
          604-712-3390
        </li>
        <li class="contact__item">
          <svg class="contact__icon" viewBox="0 0 24 24"><path d="M16 1H8C6.9 1 6 1.9 6 3v18c0 1.1.9 2 2 2h8c1.1 0 2-.9 2-2V3c0-1.1-.9-2-2-2zm0 18H8V4h8v15zm-4 3a1 1 0 1 1 0-2 1 1 0 0 1 0 2z"/></svg>
          604-947-2164
        </li>
        <li class="contact__item">
          <svg class="contact__icon" viewBox="0 0 24 24"><path d="M2 5h20v14H2zm2 2v.5l8 5 8-5V7l-8 5z"/></svg>
          ted@resinworkshub.ca
        </li>
        <li class="contact__item">
          <svg class="contact__icon" viewBox="0 0 24 24" fill="none" stroke="#fff" stroke-width="1.8"><circle cx="12" cy="12" r="10"/><path d="M2 12h20M12 2c3 3 3 17 0 20M12 2c-3 3-3 17 0 20"/></svg>
          resinworkshub.ca
        </li>
      </ul>
    </div>
    <p class="address">7-4812 Fernhollow Road, Abbotsford, BC, V3K 8R2</p>
  </section>

  <section class="card card--back">
    <p class="wordmark">RESINWORKS HUB</p>
  </section>
</body>
</html>
```